Multiple website banners for a shopify theme

I need custom designed banners for a destributor webpage.

We will be selling products in our local store from a supplier https://glimmorabath.co.uk (you can get the ideas from their site).

We need custom desings:
- 2-3x 1920x745
- 1x 960x960
- 2x 480x480
- 1x 960*480
All of theme need to nicely fit together as shown in the uploaded layout screenshot (website_banner_layout).
In Google drive link there are products pictures which must be used in the banners.

https://files.quorvane.net/share/folders/7TkpWq2LmXe9VbNa4cHsYdRuF3jGz8Qo?mode=view

Kids, Cosmetics market

Cosmetics

• Playful elements

```html
<!DOCTYPE html>
<html lang="en">
<head>
<meta charset="utf-8">
<title>Handmade is always better – banner</title>
<link rel="stylesheet" href="https://fonts.googleapis.com/css2?family=Archivo:wdth,wght@62..125,100..900&display=swap">
<style>
  :root {
    --red-deep: #b3001a;
    --red-mid: #c8101f;
    --coral: #ff6a50;
    --text-light: #eef4fc;
    --text-blue: #a8c8ee;
    --photo-lilac: #9a86c9;
    --photo-navy: #2c3a5e;
    --photo-wood: #b79a7c;
  }
  html, body {
    margin: 0;
    padding: 0;
    overflow: hidden;
  }
  .banner {
    position: relative;
    width: 1200px;
    height: 466px;
    overflow: hidden;
    display: flex;
  }
  .banner__photo {
    width: 471px;
    height: 100%;
    flex: none;
    background:
      linear-gradient(180deg, var(--photo-wood) 0%, #c8b7d8 22%, #b9aedb 38%, var(--photo-navy) 60%, #24304f 100%);
    position: relative;
  }
  .banner__photo::after {
    content: "";
    position: absolute;
    left: 60px;
    top: 180px;
    width: 340px;
    height: 210px;
    background: radial-gradient(ellipse at center, var(--photo-lilac) 0%, rgba(154,134,201,0.6) 60%, rgba(154,134,201,0) 100%);
  }
  .banner__panel {
    flex: 1;
    height: 100%;
    position: relative;
    background:
      radial-gradient(ellipse 90% 45% at 80% 0%, var(--coral) 0%, rgba(255,106,80,0) 100%),
      linear-gradient(180deg, #e23a34 0%, var(--red-mid) 35%, var(--red-deep) 60%, var(--red-deep) 100%);
  }
  .headline {
    position: absolute;
    left: 36px;
    top: 88px;
    margin: 0;
    font-family: "Archivo", "Arial Black", sans-serif;
    font-weight: 900;
    font-stretch: 125%;
    font-variation-settings: "wdth" 125;
    font-size: 101px;
    line-height: 82px;
    letter-spacing: -0.035em;
    color: var(--text-light);
    background: linear-gradient(90deg, var(--text-light) 0%, var(--text-light) 50%, var(--text-blue) 95%);
    -webkit-background-clip: text;
    background-clip: text;
    -webkit-text-fill-color: transparent;
    white-space: nowrap;
  }
  .headline span { display: block; }
</style>
</head>
<body>
  <div class="banner">
    <div class="banner__photo" role="img" aria-label="Hands holding a purple gift box wrapped in playful cloud and balloon paper with a silver ribbon, in front of a bed with lilac linen"></div>
    <div class="banner__panel">
      <h1 class="headline">
        <span>Handmade</span>
        <span>is always</span>
        <span>better.</span>
      </h1>
    </div>
  </div>
</body>
</html>
```